Meridale Bed Company Needs Business Card

Looking for a very nice looking business card. Creative but not extravagant. We sell beds and pillows across the U.S. and need something professional but catchy. I have attached the logo.

Name : Devin Holt
Title : President
Phone : (800) 471-2960
Email: sleep@quilmora.com
Website: www.quilmora.com

Can be single-sided or double-sided
horizontal or vertical

Can use Blues/Greys

Target Market(s)

Mass Market

Industry/Entity Type

Retail

Contact Information for Business Card

Name : Devin Holt
Title : President
Phone : (800) 471-2960
Email: sleep@quilmora.com
Website: www.quilmora.com

Requirements
Must have
• Clean, Modern, Smooth
• Can use Blues/Greys
• On the other side without the information - have something simple like www.quilmora.com or our logo
Nice to have
• Surprise me
Should not have
• Nothing crazy, nothing cluttered

```html
<!DOCTYPE html>
<html lang="en">
<head>
<meta charset="utf-8">
<title>Quilmora Business Card</title>
<link href="https://fonts.googleapis.com/css2?family=Ubuntu:wght@500;700&display=swap" rel="stylesheet">
<style>
  :root {
    --canvas-bg: #2b2e33;
    --card-bg: #000000;
    --brand-blue: #2fa6dc;
    --ink-white: #ffffff;
    --card-shadow: rgba(0, 0, 0, 0.55);
  }
  * { box-sizing: border-box; margin: 0; padding: 0; }
  html, body {
    width: 1200px;
    height: 1200px;
    overflow: hidden;
    background: var(--canvas-bg);
    font-family: "Ubuntu", sans-serif;
  }
  .canvas {
    position: relative;
    width: 1200px;
    height: 1200px;
  }
  .card {
    position: absolute;
    left: 150px;
    width: 900px;
    height: 514px;
    background: var(--card-bg);
    overflow: hidden;
    box-shadow: 0 14px 34px var(--card-shadow);
  }
  .card--front { top: 62px; }
  .card--back { top: 624px; }

  .stripe-field { position: absolute; }
  .card--front .stripe-field { left: 0; top: 0; width: 340px; height: 310px; }
  .card--back .stripe-field { left: 0; bottom: 0; width: 310px; height: 330px; }

  .brand-name {
    position: absolute;
    font-family: "Ubuntu", sans-serif;
    font-weight: 500;
    color: var(--brand-blue);
    line-height: 1;
    white-space: nowrap;
  }
  .card--front .brand-name {
    left: 0; right: 0;
    top: 214px;
    text-align: center;
    font-size: 128px;
  }
  .card--back .brand-name {
    left: 186px;
    top: 70px;
    font-size: 96px;
  }

  .web-line {
    position: absolute;
    left: 0; right: 0;
    top: 410px;
    text-align: center;
    font-weight: 700;
    font-size: 22px;
    letter-spacing: 0.42em;
    color: var(--ink-white);
  }
  .web-line .web-line__name { color: var(--brand-blue); }

  .contact-block {
    position: absolute;
    left: 504px;
    top: 262px;
    color: var(--ink-white);
  }
  .contact-block__name {
    font-weight: 700;
    font-size: 28px;
    line-height: 1.05;
    text-transform: uppercase;
  }
  .contact-block__title {
    font-weight: 700;
    font-size: 28px;
    line-height: 1.05;
    color: var(--brand-blue);
  }
  .contact-list {
    list-style: none;
    margin-top: 42px;
  }
  .contact-list__item {
    display: flex;
    align-items: center;
    gap: 12px;
    font-weight: 500;
    font-size: 21px;
    line-height: 32px;
  }
  .contact-list__icon {
    width: 18px;
    height: 18px;
    flex: none;
  }
</style>
</head>
<body>
<main class="canvas">

  <section class="card card--front" aria-label="Card front">
    <svg class="stripe-field" viewBox="0 0 340 310" role="img" aria-label="Diagonal blue dashed line pattern in the top-left corner">
      <defs>
        <linearGradient id="frontStripeFade" x1="0" y1="0" x2="1" y2="1">
          <stop offset="0" stop-color="#2fa6dc" stop-opacity="0.95"/>
          <stop offset="0.55" stop-color="#2fa6dc" stop-opacity="0.45"/>
          <stop offset="1" stop-color="#2fa6dc" stop-opacity="0"/>
        </linearGradient>
      </defs>
      <polygon points="0,0 330,0 0,300" fill="url(#frontStripeFade)"/>
    </svg>

    <div class="brand-name">quilmora</div>
    <p class="web-line">www.<span class="web-line__name">quilmora</span>.com</p>
  </section>

  <section class="card card--back" aria-label="Card back">
    <svg class="stripe-field" viewBox="0 0 310 330" role="img" aria-label="Diagonal blue dashed line pattern in the bottom-left corner">
      <defs>
        <linearGradient id="backStripeFade" x1="0" y1="1" x2="1" y2="0">
          <stop offset="0" stop-color="#2fa6dc" stop-opacity="0.95"/>
          <stop offset="0.55" stop-color="#2fa6dc" stop-opacity="0.45"/>
          <stop offset="1" stop-color="#2fa6dc" stop-opacity="0"/>
        </linearGradient>
      </defs>
      <polygon points="0,0 300,330 0,330" fill="url(#backStripeFade)"/>
    </svg>

    <div class="brand-name">quilmora</div>

    <div class="contact-block">
      <p class="contact-block__name">Devin Holt</p>
      <p class="contact-block__title">President</p>
      <ul class="contact-list">
        <li class="contact-list__item">
          <svg class="contact-list__icon" viewBox="0 0 18 18" aria-hidden="true">
            <path d="M2 6 Q9 1 16 6 L14 8 L12 6.5 L6 6.5 L4 8 Z" fill="#2fa6dc"/>
            <rect x="4" y="9" width="10" height="7" rx="1" fill="#2fa6dc"/>
          </svg>
          <span>(800) 471-2960</span>
        </li>
        <li class="contact-list__item">
          <svg class="contact-list__icon" viewBox="0 0 18 18" aria-hidden="true">
            <rect x="1.5" y="4" width="15" height="11" rx="1" fill="#2fa6dc"/>
            <path d="M2 5 L9 10.5 L16 5" fill="none" stroke="#000" stroke-width="1.4"/>
          </svg>
          <span>sleep@quilmora.com</span>
        </li>
        <li class="contact-list__item">
          <svg class="contact-list__icon" viewBox="0 0 18 18" aria-hidden="true">
            <g fill="none" stroke="#2fa6dc" stroke-width="1.5">
              <circle cx="9" cy="9" r="7"/>
              <ellipse cx="9" cy="9" rx="3" ry="7"/>
              <line x1="2" y1="9" x2="16" y2="9"/>
            </g>
          </svg>
          <span>www.quilmora.com</span>
        </li>
      </ul>
    </div>
  </section>

</main>
</body>
</html>
```